Business Cards for IT Consulting Company (Managed Service Provider)

I am looking to have some business cards printed and would like some designs. We are an IT Consulting company based in Vancouver BC. I would like a nice clean and modern look to the cards. I have uploaded all the versions of my logo so parts can be used as needed. Here is a snippit from our website homepage:

Quillbrook Networks Ltd. is an IT Solutions Partner located in Vancouver BC, Canada. We offer IT solutions and support to customers in the greater Vancouver Area. With expertise in Microsoft platforms, as well as Linux and Mac OSX and over 12 years experience in the IT industry, Quillbrook Networks is dedicated to offering our clients top quality service and products. We take pride in the solutions we offer our customers. The greatest compliment a client can give us is to recommend our services.

Quillbrook Networks Ltd. offers a wide range of IT services from onsite service to remote support and managed service solutions. This allows clients to choose the support path that best suits their company’s needs. Supporting many different sized companies from small to enterprise level over the past 12 years Quillbrook Networks has the experience and expertise needed to ensure things run smoothly. Allowing our clients to focus on doing business.

Revolutionizing the way IT services are delivered.

Quillbrook Networks is dedicated to providing our clients with IT solutions that work and grow with them for years to come. This philosophy helps save money in the long run instead of replacing equipment constantly. Far too often IT solutions are not well thought out and while possibly solving the problem at hand, require replacement due to growth or quality within a very short time frame. Quillbrook Networks takes pride in providing solutions that will last and be able to accommodate growth without the need for replacement.

Industry/Entity Type

Information Technology

Contact Information for Business Card

Quillbrook Networks Ltd.
(Employee Name)
Eml: (Employees Email Address)
Web: quillbrook.me
Ph: 604-555-0148

Font styles to use
Serif
Sans Serif

Requirements
Must have
• The Company logo and company colors.
Nice to have
• - Our tag line: "Revolutionizing IT Services" or "Revolutionizing the way IT services are delivered."
• - Also I really like the idea of nature and technology together blending which is sort of where my logo came from so integrating that somehow onto the business cards would be great.

```html
<!DOCTYPE html>
<html lang="en">
<head>
<meta charset="utf-8">
<title>Quillbrook Networks Ltd. – Business Cards</title>
<link href="https://fonts.googleapis.com/css2?family=Montserrat:wght@600&family=Roboto:ital,wght@0,400;0,500;1,400&display=swap" rel="stylesheet">
<style>
  :root {
    --backdrop: #a9a7a7;
    --card: #f3f3f3;
    --brand-blue: #1e8fd5;
    --ink: #3f3f41;
    --band-grey: #4a4a4c;
    --rule: #dcdcdc;
  }
  * { margin: 0; padding: 0; box-sizing: border-box; }
  html, body {
    width: 1200px; height: 1200px; overflow: hidden;
    background: var(--backdrop);
    font-family: "Roboto", Arial, sans-serif;
  }
  .canvas { position: relative; width: 1200px; height: 1200px; }

  .card {
    position: absolute;
    width: 712px; height: 418px;
    background: var(--card);
    overflow: hidden;
  }
  .card--front { left: 238px; top: 119px; }
  .card--back  { left: 231px; top: 644px; height: 417px; }

  /* Front */
  .brand {
    position: absolute; left: 110px; top: 140px;
    display: flex; align-items: center; gap: 22px;
  }
  .brand__mark {
    width: 26px; height: 26px; background: var(--brand-blue);
  }
  .brand__name {
    font-family: "Montserrat", Arial, sans-serif;
    font-weight: 600; font-size: 50px; line-height: 1;
    color: var(--brand-blue); letter-spacing: -0.5px;
  }
  .brand__name span { display: block; }
  .tagline-front {
    position: absolute; left: 0; right: 0; top: 376px;
    display: flex; justify-content: center; align-items: center; gap: 16px;
    font-size: 19px; color: var(--ink); letter-spacing: 0.2px;
  }
  .tagline-front .rule {
    display: block; width: 112px; height: 3px;
    background: linear-gradient(90deg, transparent, var(--brand-blue) 30%, var(--brand-blue) 70%, transparent);
  }

  /* Back */
  .back-brand {
    position: absolute; left: 60px; top: 172px;
    display: flex; align-items: center; gap: 16px;
  }
  .back-brand__mark {
    width: 22px; height: 22px; background: var(--brand-blue);
  }
  .back-brand__name {
    font-family: "Montserrat", Arial, sans-serif;
    font-weight: 600; font-size: 30px; line-height: 1.1;
    color: var(--brand-blue);
  }
  .back-brand__name span { display: block; }
  .divider {
    position: absolute; left: 331px; top: 80px;
    width: 1px; height: 250px; background: var(--rule);
  }
  .person { position: absolute; left: 389px; top: 122px; }
  .person__name {
    font-size: 26px; font-weight: 500; color: var(--brand-blue);
  }
  .person__role {
    margin-top: 6px; font-size: 16px; font-style: italic; color: var(--ink);
  }
  .contacts { position: absolute; left: 389px; top: 201px; list-style: none; }
  .contacts li {
    display: flex; align-items: center; gap: 17px;
    height: 27.5px; font-size: 18px; color: var(--ink);
  }
  .contacts svg { width: 18px; height: 16px; fill: var(--brand-blue); }
  .band-grey {
    position: absolute; left: 0; bottom: 0; width: 340px; height: 26px;
    background: var(--band-grey);
  }
  .band-blue {
    position: absolute; left: 314px; bottom: 0; width: 398px; height: 53px;
    background: var(--brand-blue);
    clip-path: polygon(27px 0, 100% 0, 100% 100%, 0 100%);
    display: flex; align-items: center; padding-left: 75px;
    color: #fff; font-size: 19px; letter-spacing: 0.2px;
  }
</style>
</head>
<body>
<div class="canvas">

  <section class="card card--front" aria-label="Business card front">
    <div class="brand">
      <div class="brand__mark"></div>
      <div class="brand__name"><span>Quillbrook</span><span style="font-size:22px;margin-top:6px;">Networks Ltd.</span></div>
    </div>
    <p class="tagline-front"><span class="rule"></span>Revolutionizing IT Services<span class="rule"></span></p>
  </section>

  <section class="card card--back" aria-label="Business card back">
    <div class="back-brand">
      <div class="back-brand__mark"></div>
      <div class="back-brand__name"><span>Quillbrook</span></div>
    </div>
    <div class="divider"></div>
    <div class="person">
      <p class="person__name">Daniel Brooks</p>
      <p class="person__role">Managing Director</p>
    </div>
    <ul class="contacts">
      <li>
        <svg viewBox="0 0 18 16" aria-hidden="true"><path d="M2 4c0-2 3-3 7-3s7 1 7 3v1.5h-3.5V4h-7v1.5H2z"/><path d="M4 7h10l2 7H2z"/><circle cx="9" cy="10.5" r="2" fill="#f3f3f3"/></svg>
        604-555-0148
      </li>
      <li>
        <svg viewBox="0 0 18 16" aria-hidden="true"><circle cx="9" cy="8" r="7"/><path d="M2 8h14M9 1v14M4 3.5h10M4 12.5h10" stroke="#f3f3f3" stroke-width="1" fill="none"/><ellipse cx="9" cy="8" rx="3" ry="7" stroke="#f3f3f3" stroke-width="1" fill="none"/></svg>
        www.quillbrook.me
      </li>
      <li>
        <svg viewBox="0 0 18 16" aria-hidden="true"><rect x="1" y="3" width="16" height="11"/><path d="M1 3l8 6 8-6" stroke="#f3f3f3" stroke-width="1.4" fill="none"/></svg>
        support@quillbrook.me
      </li>
    </ul>
    <div class="band-grey"></div>
    <div class="band-blue">Revolutionizing IT Services</div>
  </section>

</div>
</body>
</html>
```